Communication and Marketing agency needs a new presentation card

We are a group of communication and marketing agencies specialized in companies that are in the logistics and industrial sector. The head agency is TELVANO Grupo and the group consists of 4 agencies: TELVANO Media, TELVANO Digital, TELVANO Research and DifundeEnPantalla. We hace 4 offices in Spain (Madrid, Barcelona, Valencia and Murcia). We are looking for a clean and attractive design that transmits our experience, brand presence in the market and knowledge to those who receive the card.It has to maintain the colors of the logo that is attached.
Target Market(s)
logistics and industrial sector
Marketing department
Contact Information for Business Card
Clean and attractive design

```html
<!DOCTYPE html>
<html lang="es">
<head>
<meta charset="utf-8">
<title>TELVANO – Business card</title>
<link rel="stylesheet" href="https://fonts.googleapis.com/css2?family=Montserrat:wght@400;500;600&family=Roboto:wght@400;500&display=swap">
<style>
  :root {
    --bg: #e4e4e4;
    --paper: #ffffff;
    --brand-red: #ad2428;
    --charcoal: #524f4c;
    --stripe: #4a4746;
    --ink-white: #ffffff;
  }
  * { margin: 0; padding: 0; box-sizing: border-box; }
  html, body {
    width: 1125px; height: 1200px; overflow: hidden;
    background: var(--bg);
  }
  .card {
    position: absolute; left: 162px; width: 800px; height: 460px;
    overflow: hidden;
    box-shadow: 0 2px 4px rgba(0,0,0,.25);
  }
  .card--front { top: 100px; background: var(--paper); }
  .card--back { top: 620px; background: var(--charcoal); }

  .front-shapes { position: absolute; inset: 0; }

  .brand-mark {
    position: absolute; left: 52px; top: 50px;
    font-family: "Montserrat", sans-serif; font-weight: 500;
    color: var(--brand-red); text-align: right; line-height: 1;
  }
  .brand-mark__name { display: block; font-size: 54px; letter-spacing: 3px; }
  .brand-mark__unit { display: block; font-size: 30px; margin-top: 6px; }

  .contact {
    position: absolute; right: 36px; top: 190px;
    text-align: right; color: var(--ink-white);
  }
  .contact__name {
    font-family: "Montserrat", sans-serif; font-weight: 500;
    font-size: 26px; letter-spacing: 1px; line-height: 1.1;
  }
  .contact__role {
    font-family: "Roboto", sans-serif; font-weight: 500;
    font-size: 19px; margin-top: 4px;
  }
  .contact__list { list-style: none; margin-top: 20px; }
  .contact__item {
    font-family: "Roboto", sans-serif; font-size: 18px; line-height: 25.5px;
    display: flex; justify-content: flex-end; align-items: center; gap: 10px;
  }
  .contact__icon { width: 17px; height: 17px; flex: none; }

  .offices {
    position: absolute; right: 36px; top: 402px;
    font-family: "Montserrat", sans-serif; font-size: 18px; letter-spacing: .6px;
    color: var(--ink-white); word-spacing: 4px;
  }

  .group-mark {
    position: absolute; left: 0; right: 0; top: 150px;
    font-family: "Montserrat", sans-serif; font-weight: 500;
    color: var(--ink-white); text-align: center; line-height: 1;
  }
  .group-mark__inner { display: inline-block; text-align: right; }
  .group-mark__name { display: block; font-size: 74px; letter-spacing: 5px; }
  .group-mark__unit { display: block; font-size: 44px; margin-top: 10px; }

  .agencies {
    position: absolute; left: 0; right: 0; top: 370px;
    display: flex; justify-content: center; gap: 34px;
    font-family: "Montserrat", sans-serif; font-weight: 500; color: var(--ink-white);
  }
  .agency { text-align: right; line-height: 1; }
  .agency__name { display: block; font-size: 21px; letter-spacing: 1px; }
  .agency__unit { display: block; font-size: 13px; margin-top: 3px; }
</style>
</head>
<body>

<section class="card card--front">
  <svg class="front-shapes" width="800" height="460" viewBox="0 0 800 460" aria-hidden="true">
    <polygon points="584,0 592,0 198,460 190,460" fill="var(--stripe)"/>
    <polygon points="598,0 800,0 800,460 204,460" fill="var(--brand-red)"/>
  </svg>

  <div class="brand-mark">
    <span class="brand-mark__name">TELVANO</span>
    <span class="brand-mark__unit">Media</span>
  </div>

  <div class="contact">
    <h1 class="contact__name">ANDRÉS SOLVEIRA</h1>
    <p class="contact__role">Director</p>
    <ul class="contact__list">
      <li class="contact__item">910 482 617
        <svg class="contact__icon" viewBox="0 0 24 24" aria-hidden="true"><path fill="#fff" d="M6.6 10.8a15 15 0 0 0 6.6 6.6l2.2-2.2c.3-.3.7-.4 1-.2 1.1.4 2.3.6 3.6.6.6 0 1 .4 1 1V20c0 .6-.4 1-1 1A17 17 0 0 1 3 4c0-.6.4-1 1-1h3.5c.6 0 1 .4 1 1 0 1.3.2 2.5.6 3.6.1.3 0 .7-.2 1z"/></svg>
      </li>
      <li class="contact__item">640 275 318
        <svg class="contact__icon" viewBox="0 0 24 24" aria-hidden="true"><rect x="6" y="1.5" width="12" height="21" rx="2" fill="none" stroke="#fff" stroke-width="2"/><circle cx="12" cy="19" r="1.2" fill="#fff"/></svg>
      </li>
      <li class="contact__item">asolveira@telvano.es
        <svg class="contact__icon" viewBox="0 0 24 24" aria-hidden="true"><rect x="2" y="5" width="20" height="14" fill="#fff"/><path d="M2 5l10 8 10-8" fill="none" stroke="var(--brand-red)" stroke-width="1.8"/></svg>
      </li>
      <li class="contact__item">andressolveira
        <svg class="contact__icon" viewBox="0 0 24 24" aria-hidden="true"><rect x="3" y="3" width="18" height="18" rx="2" fill="#fff"/></svg>
      </li>
      <li class="contact__item">telvano.es
        <svg class="contact__icon" viewBox="0 0 24 24" aria-hidden="true"><circle cx="12" cy="12" r="10" fill="#fff"/><path d="M2 12h20M12 2c3 3 3 17 0 20M12 2c-3 3-3 17 0 20" fill="none" stroke="var(--brand-red)" stroke-width="1.5"/></svg>
      </li>
    </ul>
  </div>

  <p class="offices">MADRID | BARCELONA | VALENCIA | MURCIA</p>
</section>

<section class="card card--back">
  <div class="group-mark">
    <div class="group-mark__inner">
      <span class="group-mark__name">TELVANO</span>
      <span class="group-mark__unit">Grupo</span>
    </div>
  </div>

  <div class="agencies">
    <div class="agency"><span class="agency__name">TELVANO</span><span class="agency__unit">Digital</span></div>
    <div class="agency"><span class="agency__name">TELVANO</span><span class="agency__unit">Media</span></div>
    <div class="agency"><span class="agency__name">TELVANO</span><span class="agency__unit">Research</span></div>
    <div class="agency"><span class="agency__name">DIFUNDE</span><span class="agency__unit">ENPANTALLA</span></div>
  </div>
</section>

</body>
</html>
```